Manufacturer Website with Home and Product page

We have this website, veltaro.com, but we need another one for the Canadian market. Canadians like to deal with Canadians so we need to gear it to that. It will be a simpler website than the current site.

We will need a design for two pages, one for the home page and one for a product page.

I synthesized all the brief information for the designers here, descriptions for both pages are included:

https://files.brimlodge.net/doc/8qwx3Lm2Rt7Yp0KzVb4Nc6HsJd9FgA1eUi5Tr

Supporting Folder:
https://files.brimlodge.net/folder/7ZpqW3nTx8Kd2LmR5vYb0HcJs

Industry/Entity Type

Tanning Beds, Red Light Beds, Hydro massage beds

Number of Pages Required

2 page

Requirements
Must have
• Two page descriptions: https://files.brimlodge.net/doc/8qwx3Lm2Rt7Yp0KzVb4Nc6HsJd9FgA1eUi5Tr/view
Nice to have
• Information Folder: https://files.brimlodge.net/folder/u/0/7ZpqW3nTx8Kd2LmR5vYb0HcJs

```html
<!DOCTYPE html>
<html lang="en">
<head>
<meta charset="utf-8">
<title>Veltaro Canada</title>
<link href="https://fonts.googleapis.com/css2?family=Merriweather:ital,wght@1,700&family=Open+Sans:wght@400;600;700&display=swap" rel="stylesheet">
<style>
:root{
  --navy:#062b3a;
  --teal:#45d3e0;
  --coral:#e2533f;
  --ice:#d5f3f5;
  --ink:#2d3a40;
  --muted:#555f64;
  --white:#fff;
}
*{box-sizing:border-box;margin:0;padding:0}
html,body{width:1200px;height:3302px;overflow:hidden}
body{position:relative;font-family:"Open Sans",sans-serif;color:var(--ink);background:var(--white)}
.abs{position:absolute}
.serif{font-family:"Merriweather",serif;font-style:italic;font-weight:700;color:var(--navy)}
.btn{position:absolute;display:flex;align-items:center;justify-content:center;background:var(--coral);color:#fff;font-size:15px;font-weight:600;border-radius:20px;box-shadow:0 3px 8px rgba(0,0,0,.18)}

/* header */
.brand{position:absolute;display:flex;align-items:center;gap:10px;font-family:"Open Sans",sans-serif;font-weight:700;color:#5f6fb3}
.brand .mark{width:14px;height:14px;background:currentColor}
.site-header .brand{left:112px;top:40px;font-size:44px}
.phone{left:664px;top:18px;display:flex;align-items:center;gap:12px;font-size:15px;color:#333}
.phone .ico{width:40px;height:40px;border-radius:50%;background:var(--teal);display:flex;align-items:center;justify-content:center}
.catalog{left:913px;top:19px;width:175px;height:37px}
.nav{left:464px;top:76px;width:624px;display:flex;justify-content:space-between;font-size:15.5px;color:#222}

/* hero */
.hero-photo{left:0;top:0;width:1200px;height:564px;background:linear-gradient(110deg,#c8b39a 0%,#a9c7c9 35%,#e9e5df 60%,#cfe3e4 100%);z-index:-1}
.hero-badge{left:618px;top:122px;width:474px;height:474px;border-radius:50%;background:conic-gradient(from 200deg,var(--teal),var(--navy) 55%,var(--teal));}
.hero-badge .inner{position:absolute;left:16px;top:16px;right:16px;bottom:16px;border-radius:50%;background:#f6f8fb}
.hero-copy{left:655px;top:206px;width:400px;text-align:center;font-size:27px;line-height:44px;color:#333}
.hero-copy b{font-weight:600;font-size:31px;color:#222}
.hero-bed{left:672px;top:398px;width:340px;height:232px;border-radius:30px 30px 14px 14px;background:linear-gradient(180deg,#e9ecef 0%,#f7b6c8 35%,#f4f5f6 70%,#d5d9dc 100%)}

/* products */
.h2{position:absolute;left:0;width:1200px;text-align:center;font-size:54px}
.card{position:absolute;top:768px;width:386px;height:532px;background:var(--navy);box-shadow:0 8px 18px rgba(0,0,0,.15)}
.card.active{background:var(--teal)}
.card .photo{height:317px}
.card h3{position:absolute;top:372px;width:100%;text-align:center;font-size:28px;color:#fff}
.card .btn{top:438px;left:126px;width:134px;height:36px}

/* industry */
.intro{left:190px;top:1505px;width:820px;text-align:center;font-size:16px;line-height:28px;color:#444}
.tab{position:absolute;height:67px;border:2px solid var(--navy);border-radius:6px;display:flex;align-items:center;gap:12px;padding-left:18px;font-size:16px;color:var(--navy)}
.tab.on{background:var(--navy);color:#fff}
.tab svg{width:30px;height:30px;fill:none;stroke:currentColor;stroke-width:1.6}
.housing-title{left:112px;top:1860px;font-size:26px;color:#333}
.housing-text{left:112px;top:1920px;width:573px;font-size:15.5px;line-height:28.3px;text-align:justify;color:#555}

/* salon */
.quote{left:545px;top:2442px;font-size:25px;line-height:43px;color:#333}
.checks{left:556px;top:2545px;list-style:none;font-size:16px;color:#333}
.checks li{display:flex;align-items:center;gap:18px;height:34.5px}

/* footer */
.footer{left:0;top:2814px;width:1200px;height:488px;background:var(--navy);color:#fff}
.footer .brand{left:117px;top:130px;font-size:64px;color:#fff}
.socials{left:111px;top:236px;display:flex;gap:17px}
.socials span{width:34px;height:34px;border:1.5px solid #fff;border-radius:50%}
.fhead{font-size:16px;letter-spacing:.2px}
.fhead::after{content:"";display:block;width:40px;height:2px;background:#fff;margin-top:10px}
.flist{font-size:13.5px;line-height:25.7px}
.rule{left:112px;top:329px;width:976px;height:1px;background:rgba(255,255,255,.25)}
.legal{left:110px;top:381px;width:980px;text-align:center;font-size:12px;line-height:25.6px}
</style>
</head>
<body>

<header class="site-header">
  <div class="brand"><span>Veltaro</span><span class="mark"></span></div>
  <div class="abs phone"><span class="ico"><svg width="20" height="20" viewBox="0 0 24 24" fill="#fff"><path d="M6.6 10.8a15 15 0 0 0 6.6 6.6l2.2-2.2c.3-.3.7-.4 1-.2 1.1.4 2.3.6 3.6.6.6 0 1 .4 1 1V20c0 .6-.4 1-1 1A17 17 0 0 1 3 4c0-.6.4-1 1-1h3.5c.6 0 1 .4 1 1 0 1.3.2 2.5.6 3.6.1.3 0 .7-.2 1z"/></svg></span><span>Call Us: <b>416.555.0182</b></span></div>
  <div class="btn catalog">Request a Catalog</div>
  <nav class="abs nav"><span>Home</span><span>Tanning</span><span>Massage</span><span>Red Light</span><span>Salon Startup</span><span>About Us</span><span>Contact Us</span></nav>
</header>

<section class="hero">
  <div class="abs hero-photo" role="img" aria-label="Smiling woman relaxing on a lounge chair by the sea"></div>
  <svg class="abs" style="left:0;top:530px;z-index:0" width="1200" height="60" viewBox="0 0 1200 60"><path fill="#fff" d="M0 30 L40 22 80 34 130 20 190 32 250 18 320 30 380 24 450 36 520 22 600 34 680 20 760 32 840 24 920 36 1000 22 1080 30 1140 20 1200 28 V60 H0Z"/></svg>
  <div class="abs hero-badge"><div class="inner"></div></div>
  <p class="abs hero-copy">The Leading Manufacturer<br>in <b>Commercial Tanning,</b><br><b>Red Light</b> and <b>Water</b><br><b>Massage Therapy</b></p>
  <div class="abs hero-bed" role="img" aria-label="Open red light bed with pink lamps"></div>
</section>

<section class="products">
  <h2 class="h2 serif" style="top:646px">Product Type</h2>
  <article class="card" style="left:14px">
    <div class="photo" role="img" aria-label="Couple on a beach beside a stand-up tanning booth" style="background:linear-gradient(180deg,#b9c7d3,#d8c9b0 60%,#b88fcf)"></div>
    <h3 class="serif">Tanning Beds</h3><div class="btn">Learn More</div>
  </article>
  <article class="card active" style="left:408px">
    <div class="photo" role="img" aria-label="Hydro massage bed with control screen" style="background:linear-gradient(180deg,#f1e9e5 0%,#eef0f2 50%,#2ba4b4 100%)"></div>
    <h3 class="serif">Hydro Massage</h3><div class="btn">Learn More</div>
  </article>
  <article class="card" style="left:800px">
    <div class="photo" role="img" aria-label="Red light bed with glowing pink lamps" style="background:linear-gradient(180deg,#f6cfd9,#f0b4c6 60%,#c07ac4)"></div>
    <h3 class="serif">Red Light Beds</h3><div class="btn">Learn More</div>
  </article>
</section>

<section class="industry">
  <h2 class="h2 serif" style="top:1414px">Industry Application Section</h2>
  <p class="abs intro">We need to incorporate this section in a different way that matches this site. You can use the same images for the industries but it would be better to get new ones.</p>
  <div class="tab on" style="left:158px;top:1597px;width:165px"><svg viewBox="0 0 30 30"><path d="M4 14 15 4l11 10M7 12v14h16V12M12 26v-8h6v8"/></svg>HOUSING</div>
  <div class="tab" style="left:333px;top:1597px;width:166px"><svg viewBox="0 0 30 30"><rect x="8" y="10" width="10" height="16" rx="2"/><path d="M10 6h6v4M20 16h6v10h-6z"/></svg>MEDICAL</div>
  <div class="tab" style="left:509px;top:1597px;width:165px"><svg viewBox="0 0 30 30"><path d="M15 26S4 19 4 11a5.5 5.5 0 0 1 11-2 5.5 5.5 0 0 1 11 2c0 8-11 15-11 15z"/><path d="M7 15h5l2-4 3 7 2-3h4"/></svg>FITNESS</div>
  <div class="tab" style="left:685px;top:1597px;width:173px"><svg viewBox="0 0 30 30"><circle cx="15" cy="13" r="7"/><path d="M6 27c2-5 16-5 18 0M8 8c-4 3-4 9 0 12M22 8c4 3 4 9 0 12"/></svg>BEAUTY/SPA</div>
  <div class="tab" style="left:868px;top:1597px;width:174px"><svg viewBox="0 0 30 30"><path d="M3 24h24M5 24v-6h20v6M9 18v-3h8v3"/><circle cx="21" cy="7" r="3"/></svg>TANNING</div>
  <div class="tab" style="left:382px;top:1674px;width:178px"><svg viewBox="0 0 30 30"><path d="M4 22h22M6 22a9 9 0 0 1 18 0M15 13v-3M13 10h4M5 26h20"/></svg>HOSPITALITY</div>
  <div class="tab" style="left:573px;top:1674px;width:245px"><svg viewBox="0 0 30 30"><rect x="4" y="9" width="22" height="16" rx="2"/><path d="M11 9V6h8v3M4 16h22"/></svg>CORPORATE WELLNESS</div>

  <h3 class="abs housing-title serif">Housing</h3>
  <p class="abs housing-text">Distinguish your community by providing a comprehensive range of amenities to your residents. From top-of-the-line commercial tanning equipment to the revolutionary AquaVela, the world's first and only trackless water massage bed, housing offices can leverage these products as enticing perks or optional amenities to promote wellness within the community and attract prospective residents. By offering such exceptional features, you create an environment that prioritizes well-being and sets your community apart from the competition, making it an irresistible choice for those seeking a vibrant and health-conscious living experience.</p>
  <div class="abs" style="left:741px;top:1813px;width:329px;height:413px;background:var(--ice)"></div>
  <div class="abs" role="img" aria-label="Smiling woman in a sun hat and sunglasses" style="left:759px;top:1831px;width:329px;height:412px;background:linear-gradient(160deg,#e7c7a5,#c8875a 55%,#e9cfb2)"></div>
</section>

<section class="salon">
  <h2 class="h2 serif" style="top:2316px">Salon Startup Section</h2>
  <div class="abs" style="left:132px;top:2411px;width:373px;height:333px;background:var(--ice)"></div>
  <div class="abs" role="img" aria-label="Woman relaxing on cushions among plants" style="left:115px;top:2424px;width:375px;height:334px;background:linear-gradient(120deg,#6e7a58,#cdbba3 50%,#efe7dc)"></div>
  <p class="abs quote serif" style="color:#333">“Starting a Salon or Spa?”<br>“We’ve done it 100s of Times and Will Help You”</p>
  <ul class="abs checks">
    <li><svg width="14" height="14" viewBox="0 0 14 14"><circle cx="7" cy="7" r="6" fill="none" stroke="#45d3e0" stroke-width="1.5"/><path d="M4 7l2 2 4-4" fill="none" stroke="#45d3e0" stroke-width="1.5"/></svg>Develop a Business Plan</li>
    <li><svg width="14" height="14" viewBox="0 0 14 14"><circle cx="7" cy="7" r="6" fill="none" stroke="#45d3e0" stroke-width="1.5"/><path d="M4 7l2 2 4-4" fill="none" stroke="#45d3e0" stroke-width="1.5"/></svg>Space Design</li>
    <li><svg width="14" height="14" viewBox="0 0 14 14"><circle cx="7" cy="7" r="6" fill="none" stroke="#45d3e0" stroke-width="1.5"/><path d="M4 7l2 2 4-4" fill="none" stroke="#45d3e0" stroke-width="1.5"/></svg>Review Financing Options</li>
    <li><svg width="14" height="14" viewBox="0 0 14 14"><circle cx="7" cy="7" r="6" fill="none" stroke="#45d3e0" stroke-width="1.5"/><path d="M4 7l2 2 4-4" fill="none" stroke="#45d3e0" stroke-width="1.5"/></svg>Starup Marketing</li>
  </ul>
  <div class="btn" style="left:556px;top:2705px;width:134px;height:36px">Learn More</div>
</section>

<svg class="abs" style="left:0;top:2796px" width="1200" height="24" viewBox="0 0 1200 24"><path fill="#062b3a" d="M0 16 L50 10 110 18 170 6 240 16 300 8 370 18 440 6 510 16 580 10 650 18 720 6 790 16 860 8 930 18 1000 6 1070 16 1130 8 1200 14 V24 H0Z"/></svg>
<footer class="abs footer">
  <div class="brand"><span>Veltaro</span><span class="mark"></span></div>
  <div class="abs socials"><span></span><span></span><span></span><span></span><span></span><span></span></div>
  <div class="abs" style="left:474px;top:84px"><div class="fhead">CONTACT US</div>
    <div class="flist" style="margin-top:18px"><b>Veltaro International</b><br>1180 Harbour Ave. North, Clearwater,<br>FL 33755<br><b>Sales:</b> 727-555-0143<br><b>Parts &amp; Services:</b> 800.555.0176<br><b>Main Line:</b> 800.555.0129</div></div>
  <div class="abs" style="left:765px;top:84px"><div class="fhead">QUICK LINKS</div>
    <div class="flist" style="margin-top:18px">Commercial Tanning<br>Customer Service<br>Wellness Products<br>About Us<br>Replacement Lamps and Parts<br>Contact Veltaro</div></div>
  <div class="abs flist" style="left:990px;top:138px">Salon Startup<br>Blog<br>Financing<br>Terms of Service<br>Privacy Policy</div>
  <div class="abs rule"></div>
  <p class="abs" style="left:0;top:359px;width:1200px;text-align:center;font-size:13px">© 2023 Veltaro International. All Rights Reserved</p>
  <p class="abs legal">Tanning 510(k):K204417 • Contraindication: This Product Is Contraindicated For Use On Persons Under The Age Of 18 Years. “Contraindication: This Product Must Not Be Used If Skin Lesions Or Open Wounds Are Present.” “Warning: This Product Should Not Be Used On Individuals Who Have Had Skin Cancer Or Have A Family History Of Skin Cancer.” “Warning: Persons Repeatedly Exposed To UV Radiation Should Be Regularly Evaluated For Skin Cancer.</p>
</footer>

</body>
</html>
```